MRT Property - Business Cards

Looking for a business card & general letterhead, signage etc design for our new logo.

Colours:
000a20
0056a2
00b5ef
0088ce
68cef2

Fonts:
Poppins
Karla

Please keep look and feel of new brand - example in the zip package I sent.

```html
<!DOCTYPE html>
<html lang="en">
<head>
<meta charset="utf-8">
<title>MRT Property – Business Cards</title>
<link href="https://fonts.googleapis.com/css2?family=Poppins:wght@400;500;700&display=swap" rel="stylesheet">
<style>
  :root {
    --ink: #000a20;
    --navy: #0056a2;
    --cyan: #00b5ef;
    --mid-blue: #0088ce;
    --sky: #68cef2;
    --stage: #1e1e1e;
    --silver-light: #ececec;
    --silver-dark: #c4c4c4;
    --white: #ffffff;
  }
  * { box-sizing: border-box; margin: 0; padding: 0; }
  html, body {
    width: 1200px;
    height: 1015px;
    overflow: hidden;
    background: var(--stage);
    font-family: "Poppins", sans-serif;
  }
  .canvas {
    width: 1200px;
    height: 1015px;
    display: flex;
    flex-direction: column;
    align-items: center;
    justify-content: center;
    gap: 44px;
  }
  .card {
    width: 760px;
    height: 434px;
    position: relative;
    box-shadow: 0 18px 40px rgba(0, 0, 0, 0.55);
    overflow: hidden;
  }
  .card-front {
    background: linear-gradient(135deg, var(--silver-light) 0%, #dcdcdc 50%, var(--silver-dark) 100%);
    display: flex;
    align-items: center;
    justify-content: center;
  }
  .brand {
    display: flex;
    align-items: center;
    gap: 22px;
  }
  .brand-dot {
    width: 58px;
    height: 58px;
    border-radius: 50%;
    background: var(--navy);
  }
  .brand-name {
    font-weight: 700;
    font-size: 64px;
    letter-spacing: 1px;
    color: var(--navy);
  }
  .card-back {
    background: radial-gradient(ellipse at 35% 25%, #2a9ad6 0%, #1b7fcc 35%, #1463bd 70%, #0d50ad 100%);
    color: var(--white);
    display: flex;
    flex-direction: column;
    align-items: center;
    justify-content: center;
    text-align: center;
  }
  .holder-name {
    font-weight: 700;
    font-size: 34px;
    letter-spacing: 1px;
    line-height: 1.1;
  }
  .holder-role {
    font-size: 19px;
    font-weight: 500;
    margin-top: 2px;
  }
  .divider {
    width: 300px;
    height: 1px;
    background: rgba(255, 255, 255, 0.45);
    margin: 10px 0;
  }
  .contact-icons {
    display: flex;
    gap: 8px;
    margin: 2px 0;
  }
  .contact-icons svg { width: 30px; height: 26px; display: block; }
  .contact-list {
    list-style: none;
    font-size: 20px;
    font-weight: 500;
    line-height: 1.3;
  }
  .address {
    font-size: 20px;
    font-weight: 500;
    line-height: 1.3;
  }
</style>
</head>
<body>
<main class="canvas">
  <section class="card card-front" aria-label="Business card front">
    <div class="brand">
      <span class="brand-dot" aria-hidden="true"></span>
      <span class="brand-name">MRT Property</span>
    </div>
  </section>

  <section class="card card-back" aria-label="Business card back">
    <h1 class="holder-name">DANIEL HART</h1>
    <p class="holder-role">Managing Director</p>
    <div class="divider"></div>
    <div class="contact-icons" aria-hidden="true">
      <svg viewBox="0 0 30 26">
        <rect width="30" height="26" rx="4" fill="#fff"/>
        <path d="M8 9c2-3 12-3 14 0l-2 2-3-1v-2c-2-1-2-1-4 0v2l-3 1z" fill="#0056a2"/>
        <rect x="10" y="12" width="10" height="7" rx="1.5" fill="#0056a2"/>
      </svg>
      <svg viewBox="0 0 30 26">
        <rect width="30" height="26" rx="4" fill="#fff"/>
        <rect x="7" y="7" width="16" height="12" fill="#0056a2"/>
        <path d="M7 7l8 7 8-7" stroke="#fff" stroke-width="1.4" fill="none"/>
      </svg>
      <svg viewBox="0 0 30 26">
        <rect width="30" height="26" rx="4" fill="#fff"/>
        <circle cx="15" cy="13" r="7" fill="#0056a2"/>
        <ellipse cx="15" cy="13" rx="3" ry="7" stroke="#fff" stroke-width="1" fill="none"/>
        <path d="M8 13h14" stroke="#fff" stroke-width="1"/>
      </svg>
    </div>
    <div class="divider"></div>
    <ul class="contact-list">
      <li>044-987 654 321</li>
      <li>hello@mrtproperty.com</li>
      <li>www.mrtproperty.com</li>
    </ul>
    <div class="divider"></div>
    <p class="address">18, Harbour View Road<br>40210, Westland</p>
  </section>
</main>
</body>
</html>
```